Business Cards for a law firm

Business cards for our law firm. Use our silhoette logo and OAK PARTNERS - check our website (www.oakpartners.example)

Contact Information for Business Card

our silhouette logo, OAK PARTNERS, 800-555-0147, Dorian Pemberton, dorian@oakpartners.example

Requirements
Must have
• our silhouette logo, OAK PARTNERS, 800-555-0147, Dorian Pemberton, dorian@oakpartners.example

```html
<!DOCTYPE html>
<html lang="en">
<head>
<meta charset="utf-8">
<title>Oak Partners Business Cards</title>
<link rel="stylesheet" href="https://fonts.googleapis.com/css2?family=Michroma&family=Poppins:wght@400;500;600&display=swap">
<style>
  :root {
    --navy: #1a316c;
    --white: #ffffff;
    --backdrop: #8a8a8a;
    --navy-soft: #5b6f9f;
    --navy-pale: #c9d2e6;
  }
  * { margin: 0; padding: 0; box-sizing: border-box; }
  html, body { width: 1093px; height: 1200px; overflow: hidden; }
  body { background: var(--backdrop); position: relative; font-family: "Poppins", sans-serif; }

  .card { position: absolute; left: 264px; width: 580px; height: 357px; overflow: hidden; }
  .card-front { top: 226px; background: var(--white); }
  .card-back { top: 620px; background: var(--navy); }

  .brand-art {
    position: absolute; left: 15px; top: 0; width: 238px; height: 344px;
    background: linear-gradient(180deg, var(--navy-pale) 0%, var(--navy-soft) 100%);
  }
  .base-band { position: absolute; left: 0; bottom: 0; width: 100%; height: 13px; background: var(--navy); }

  .firm-name {
    position: absolute; left: 283px; top: 70px;
    font-family: "Michroma", sans-serif; font-size: 18px; letter-spacing: 2px;
    color: var(--navy);
  }
  .person-name {
    position: absolute; left: 282px; top: 188px;
    font-family: "Michroma", sans-serif; font-size: 15px; letter-spacing: 0.5px;
    color: var(--navy);
  }
  .contact-list { position: absolute; left: 281px; top: 234px; list-style: none; }
  .contact-item { display: flex; align-items: center; height: 26px; color: #222; font-size: 15px; }
  .contact-item.phone { font-size: 22px; font-weight: 500; color: var(--navy); height: 30px; }
  .contact-icon { width: 24px; height: 24px; margin-right: 6px; flex: none; }
  .contact-item .accent { color: var(--navy); }

  .back-logo {
    position: absolute; left: 0; right: 0; top: 150px;
    display: flex; justify-content: center; align-items: center; gap: 16px;
  }
  .back-mark { width: 22px; height: 22px; background: var(--white); }
  .back-firm-name {
    font-family: "Michroma", sans-serif; font-size: 28px; letter-spacing: 3px; color: var(--white);
  }
  .back-phone {
    position: absolute; left: 0; right: 0; top: 276px;
    display: flex; justify-content: center; align-items: center; gap: 16px;
    color: var(--white); font-weight: 600; font-size: 30px; letter-spacing: 3px;
  }
  .back-phone-icon { width: 40px; height: 40px; }
</style>
</head>
<body>
  <section class="card card-front">
    <div class="brand-art" role="img" aria-label="Brand silhouette artwork of two standing figures"></div>
    <div class="base-band"></div>
    <h1 class="firm-name">OAK PARTNERS</h1>
    <h2 class="person-name">DORIAN PEMBERTON</h2>
    <ul class="contact-list">
      <li class="contact-item phone">
        <svg class="contact-icon" viewBox="0 0 24 24" aria-hidden="true">
          <circle cx="12" cy="12" r="11" fill="none" stroke="#1a316c" stroke-width="1.3"/>
          <path d="M8 7.5c.6-.6 1.3-.5 1.7.1l.9 1.4c.3.5.2 1-.2 1.3l-.6.5c.5 1.3 1.6 2.4 2.9 2.9l.5-.6c.3-.4.8-.5 1.3-.2l1.4.9c.6.4.7 1.1.1 1.7-1 1-2.7 1-4.5-.4-1.8-1.4-3.2-3-4-4.9-.5-1.3-.4-2.1.5-2.7z" fill="#1a316c"/>
        </svg>
        800-555-0147
      </li>
      <li class="contact-item">
        <svg class="contact-icon" viewBox="0 0 24 24" aria-hidden="true">
          <circle cx="12" cy="12" r="11" fill="none" stroke="#1a316c" stroke-width="1.3"/>
          <rect x="7" y="8.5" width="10" height="7" fill="#1a316c"/>
          <path d="M7 8.5l5 4 5-4" fill="none" stroke="#fff" stroke-width="0.9"/>
        </svg>
        dorian@oakpartners.example
      </li>
      <li class="contact-item">
        <svg class="contact-icon" viewBox="0 0 24 24" aria-hidden="true">
          <circle cx="12" cy="12" r="11" fill="none" stroke="#1a316c" stroke-width="1.3"/>
          <circle cx="12" cy="12" r="5" fill="none" stroke="#1a316c" stroke-width="1.1"/>
          <ellipse cx="12" cy="12" rx="2.2" ry="5" fill="none" stroke="#1a316c" stroke-width="0.9"/>
          <path d="M7 12h10M7.8 9.5h8.4M7.8 14.5h8.4" stroke="#1a316c" stroke-width="0.8"/>
        </svg>
        www.<span class="accent">oakpartners</span>.example
      </li>
    </ul>
  </section>

  <section class="card card-back">
    <div class="back-logo">
      <span class="back-mark" aria-hidden="true"></span>
      <span class="back-firm-name">OAK PARTNERS</span>
    </div>
    <div class="back-phone">
      <svg class="back-phone-icon" viewBox="0 0 40 40" aria-hidden="true">
        <circle cx="20" cy="20" r="19" fill="#fff"/>
        <path d="M13 12.5c1-1 2.2-.8 2.8.2l1.5 2.3c.5.8.3 1.6-.3 2.1l-1 .8c.8 2.2 2.6 4 4.8 4.8l.8-1c.5-.6 1.3-.8 2.1-.3l2.3 1.5c1 .6 1.2 1.8.2 2.8-1.7 1.7-4.5 1.6-7.4-.7-3-2.3-5.3-5-6.6-8.1-.8-2.2-.7-3.5.8-4.4z" fill="#1a316c"/>
        <path d="M22 11a7 7 0 0 1 7 7M22 14.5a3.5 3.5 0 0 1 3.5 3.5" fill="none" stroke="#1a316c" stroke-width="1.6" stroke-linecap="round"/>
      </svg>
      <span>(800) 555 -0147</span>
    </div>
  </section>
</body>
</html>
```